Halvorn Current Electric van design

Looking to design a wrap for a 2021 veltrana roamhaul high roof using orange black and dark grey colors like in the logo

```html
<!DOCTYPE html>
<html lang="en">
<head>
<meta charset="utf-8">
<title>Halvorn Current Electric – Van Wrap Layout</title>
<link rel="stylesheet" href="https://fonts.googleapis.com/css2?family=Montserrat:wght@400;800&family=Barlow:wght@500;600&display=swap">
<style>
  :root {
    --wrap-orange: #e06442;
    --wrap-black: #000000;
    --wrap-white: #ffffff;
    --dark-grey: #444444;
    --text-dark: #1a1a1a;
    --partner-grey: #333333;
  }
  * { margin: 0; padding: 0; box-sizing: border-box; }
  html, body {
    width: 1200px;
    height: 1010px;
    overflow: hidden;
    background: var(--dark-grey);
  }
  .wrap-panel {
    position: absolute;
    left: 40px;
    top: 317px;
    width: 1120px;
    height: 375px;
    background: var(--wrap-white);
    overflow: hidden;
  }
  .panel-graphic {
    position: absolute;
    inset: 0;
    width: 100%;
    height: 100%;
  }
  .brand-block {
    position: absolute;
    left: 379px;
    top: 38px;
    display: flex;
    align-items: center;
    gap: 22px;
  }
  .brand-dot {
    width: 90px;
    height: 90px;
    border-radius: 50%;
    background: var(--wrap-orange);
    flex-shrink: 0;
  }
  .brand-name {
    color: var(--text-dark);
    font-family: "Montserrat", sans-serif;
    line-height: 1;
  }
  .brand-name .name-top {
    display: block;
    font-weight: 800;
    font-size: 33px;
    letter-spacing: 4px;
  }
  .brand-name .name-bottom {
    display: block;
    font-weight: 400;
    font-size: 33px;
    margin-top: 4px;
    letter-spacing: -0.3px;
  }
  .service-list {
    list-style: none;
  }
  .service-item {
    position: absolute;
    display: flex;
    align-items: center;
    gap: 4px;
    font-family: "Barlow", sans-serif;
    font-weight: 500;
    font-size: 11px;
    color: var(--text-dark);
    letter-spacing: 0.3px;
    transform: translateY(-50%);
    white-space: nowrap;
  }
  .service-arrow {
    width: 14px;
    height: 8px;
    flex-shrink: 0;
  }
  .partner-row {
    position: absolute;
    left: 240px;
    top: 269px;
    display: flex;
    align-items: center;
    gap: 20px;
  }
  .partner-name {
    font-family: "Barlow", sans-serif;
    font-weight: 600;
    font-size: 15px;
    color: var(--partner-grey);
    letter-spacing: 0.5px;
    text-transform: uppercase;
  }
</style>
</head>
<body>
  <section class="wrap-panel" aria-label="Side wrap layout for Halvorn Current Electric van">
    <svg class="panel-graphic" viewBox="0 0 1790 600" preserveAspectRatio="none" aria-hidden="true">
      <polygon class="rear-black" points="985,600 1407,0 1790,0 1790,600" fill="var(--wrap-black)"/>
      <polygon class="orange-peak" points="1422,7 1047,600 1632,600" fill="var(--wrap-orange)" stroke="var(--wrap-white)" stroke-width="14" stroke-linejoin="miter"/>
    </svg>

    <div class="brand-block">
      <div class="brand-dot" aria-hidden="true"></div>
      <h1 class="brand-name">
        <span class="name-top">HALVORN</span>
        <span class="name-bottom">Current Electric</span>
      </h1>
    </div>

    <ul class="service-list">
      <li class="service-item" style="right:373px; top:158px;">Generator Installation<svg class="service-arrow" viewBox="0 0 14 8"><polygon points="0,4 5,0 5,2 14,2 14,6 5,6 5,8" fill="var(--wrap-orange)"/></svg></li>
      <li class="service-item" style="right:385px; top:176px;">Service Upgrades<svg class="service-arrow" viewBox="0 0 14 8"><polygon points="0,4 5,0 5,2 14,2 14,6 5,6 5,8" fill="var(--wrap-orange)"/></svg></li>
      <li class="service-item" style="right:395px; top:194px;">Low Voltage Wiring<svg class="service-arrow" viewBox="0 0 14 8"><polygon points="0,4 5,0 5,2 14,2 14,6 5,6 5,8" fill="var(--wrap-orange)"/></svg></li>
      <li class="service-item" style="right:407px; top:211px;">3-Phase Service<svg class="service-arrow" viewBox="0 0 14 8"><polygon points="0,4 5,0 5,2 14,2 14,6 5,6 5,8" fill="var(--wrap-orange)"/></svg></li>
      <li class="service-item" style="right:420px; top:228px;">Equipment Connections<svg class="service-arrow" viewBox="0 0 14 8"><polygon points="0,4 5,0 5,2 14,2 14,6 5,6 5,8" fill="var(--wrap-orange)"/></svg></li>
      <li class="service-item" style="right:433px; top:247px;">Emergency Lighting<svg class="service-arrow" viewBox="0 0 14 8"><polygon points="0,4 5,0 5,2 14,2 14,6 5,6 5,8" fill="var(--wrap-orange)"/></svg></li>
      <li class="service-item" style="right:446px; top:268px;">Code Violations<svg class="service-arrow" viewBox="0 0 14 8"><polygon points="0,4 5,0 5,2 14,2 14,6 5,6 5,8" fill="var(--wrap-orange)"/></svg></li>
      <li class="service-item" style="right:459px; top:286px;">Warehouse Lighting<svg class="service-arrow" viewBox="0 0 14 8"><polygon points="0,4 5,0 5,2 14,2 14,6 5,6 5,8" fill="var(--wrap-orange)"/></svg></li>
    </ul>

    <div class="partner-row">
      <span class="partner-name">Torvane</span>
      <span class="partner-name">Kelmark</span>
      <span class="partner-name">Brightwell</span>
    </div>
  </section>
</body>
</html>
```